Flyer-Design für Hundephysiopraxis
Zielgruppe
Ich bin selbstständige Hundephysiotherapeutin / Hundeosteopathin /Hundefitnesstrainerin. Meine Zielgruppe sind Hundehalter bzw. allgemein Tierhalter (biete noch weitere Dinge für Hunde/Tiere an) aber auch Tierärzte.
Aufgabenstellung
Es wäre schön, wenn Sie die Texte ähnlich wie auf meiner Homepage gestalten (z.B. Infos aus der Startseite oder Therapieformen).
Prinzipiell sollte es eher natürlich, freundlich und nett gestaltet sein. Schlichtere Farben passend zum Logo.
Homepage: www.pfotenruhe-mitte.de
Bei den Maßen bin ich offen, hatte aber eher an diesen 'typischen Flyer' gedacht (3 seitiger Flyer mit Vorder und Rückseite) bin aber prinzipiell offen :)
Einen Beispiel Flyer habe ich drangehängt sowie z.B. schon ein paar Fotos die man ggf nutzen kann. Weitere Behandlunsfotos kann ich gerne nachreichen.
Die Flyer sollen hauptsächlich bei z.B. Tierärzten / Tierklinik / Tiernahrungsmärkte wie Kornbeutel ausgelegt werden damit Menschen die mich noch nicht kennen auf meine Arbeit aufmerksam werden.

```html
<!DOCTYPE html>
<html lang="de">
<head>
<meta charset="utf-8">
<title>Pfotenruhe Mitte – Flyer Hundephysiotherapie</title>
<link href="https://fonts.googleapis.com/css2?family=Open+Sans:wght@400;600;800&display=swap" rel="stylesheet">
<style>
:root{
  --stage:#e7a07f;
  --flyer:#ef9458;
  --brown:#9c5533;
  --cream:#fbe3d3;
  --white:#ffffff;
  --photo-green:#7fa65a;
  --photo-warm:#d9b89a;
  --photo-dog:#c9864f;
}
*{box-sizing:border-box;margin:0;padding:0}
html,body{width:1200px;height:912px;overflow:hidden}
body{background:var(--stage);font-family:"Open Sans",Arial,sans-serif;color:var(--white);position:relative}

.brand{position:absolute;top:22px;left:0;width:1200px;text-align:center}
.brand-mark{display:inline-flex;align-items:center;gap:12px}
.brand-dot{width:34px;height:34px;border:2px solid var(--white);border-radius:50%}
.brand-name{font-size:34px;font-weight:600;letter-spacing:.5px}
.brand-sub{font-size:12px;letter-spacing:4px;margin-top:4px;line-height:1.5}

.flyer{position:absolute;left:80px;top:146px;width:1040px;height:740px;background:var(--flyer);overflow:hidden;box-shadow:0 6px 18px rgba(120,50,20,.25)}
.fold{position:absolute;top:0;bottom:0;width:1px;background:rgba(120,50,20,.18)}
.fold--1{left:347px}.fold--2{left:694px}

.panel{position:absolute;top:0;height:100%}
.panel--intro{left:0;width:347px;padding:26px 24px}
.panel--services{left:347px;width:347px;padding:26px 20px}
.panel--about{left:694px;width:346px;padding:34px 20px 20px 22px}

.headline{font-weight:800;font-size:20px;line-height:1.15;text-align:center;margin-bottom:14px}
.intro-text{font-size:9.4px;line-height:1.45;text-align:center;margin-bottom:9px}

.hero-hill{position:absolute;left:0;bottom:0;width:347px;height:330px}
.hero-photo{position:absolute;left:95px;bottom:40px;width:170px;height:270px;border-radius:80px 80px 10px 10px;background:linear-gradient(160deg,var(--photo-dog),#e9d2bd)}

.section-title{font-size:13px;font-weight:400;margin:0 0 6px}
.bullets{list-style:none;font-size:8.6px;line-height:1.5;margin-bottom:14px}
.bullets li::before{content:"• "}
.note{font-size:8.6px;line-height:1.45;margin-bottom:14px;width:190px}
.services-col{width:200px}
.silhouette{position:absolute;left:70px;bottom:26px;width:90px;height:80px;border-radius:40% 50% 20% 30%;background:var(--brown);opacity:.8}

.photo-circle{position:absolute;width:130px;height:130px;border-radius:50%}
.photo-circle--one{left:584px;top:160px;background:radial-gradient(circle at 40% 40%,#f2f2f2 0 20%,var(--photo-green) 60%)}
.photo-circle--two{left:574px;top:330px;border-radius:28px;background:linear-gradient(180deg,var(--photo-green),#5d8a3e 70%,#b37ad6)}
.photo-circle--three{left:584px;top:500px;background:radial-gradient(circle at 45% 40%,#ffffff 0 18%,var(--photo-warm) 60%)}

.wave{position:absolute;right:0;top:0;width:260px;height:150px}
.about-block{margin-left:44px;position:relative}
.about-title{font-size:12.5px;font-weight:400;margin:12px 0 5px}
.about-text{font-size:8.4px;line-height:1.45;margin-bottom:6px}
.about-block .bullets{margin-bottom:6px;font-size:8.4px}
.footer{position:absolute;left:740px;bottom:10px;font-size:7px;color:rgba(255,255,255,.75)}
</style>
</head>
<body>

<header class="brand">
  <div class="brand-mark"><span class="brand-dot"></span><span class="brand-name">Pfotenruhe Mitte</span></div>
  <div class="brand-sub">Hundephysiotherapie<br>Mara Hollweg</div>
</header>

<main class="flyer">
  <div class="fold fold--1"></div><div class="fold fold--2"></div>

  <section class="panel panel--intro">
    <h1 class="headline">Hundephysiotherapie<br>&amp; Hundeosteopathie (i.A.)</h1>
    <p class="intro-text">In der Humanmedizin wird die Physiotherapie bei der Genesung der Patienten schon selbstverständlich und unterstützend eingesetzt. Tiere können an ähnlichen Problemen leiden wie wir Menschen. Sie haben genau so Schmerzen und dies schränkt ihr Leben oftmals ein. Wir können unsere Schmerzen äußern. Viele Hunde jedoch leben mit diesem Schmerz viele Wochen, ehe es unerträglich wird und sie lahmen oder andere Dinge anzeigen. Gerade deshalb ist die Physiotherapie so enorm wichtig, damit unsere Hunde unbeschwert und ohne Schmerzen lange an unserer Seite bleiben.</p>
    <p class="intro-text">Jeder Körper ist ein individuelles und komplexes System mit eigenen Anforderungen an Beanspruchungen, Intensitäten und Erholungsphasen. Entsprechend umfangreich aufgestellt ist das Therapiespektrum meiner Arbeit. Dabei immer im Fokus: Die stets vollkommen individuellen Therapieprogramme, in enger Zusammenarbeit mit dem Tierarzt. Sensibel abgestimmt auf die spezifischen Anforderungen der einzelnen Krankheitsbilder. Jeder Hund hat eine andere Hintergrundgeschichte und auch dies berücksichtige ich bei meinen Therapien. Mein Ziel ist es, die Lebensfreude und Lebensqualität unserer Vierbeiner zu erhalten oder gar zu verbessern.</p>
    <svg class="hero-hill" viewBox="0 0 347 330" aria-hidden="true">
      <path d="M0 120 C60 60 120 110 150 200 C170 260 230 270 347 300 L347 330 L0 330 Z" fill="var(--brown)"/>
    </svg>
    <div class="hero-photo" role="img" aria-label="Foto: aufgerichteter Jagdhund mit weiß-braunem Fell, umgeben von Pfotenmotiven"></div>
  </section>

  <section class="panel panel--services">
    <div class="services-col">
      <h2 class="section-title">Einsatzmöglichkeiten der Physiotheraphie:</h2>
      <ul class="bullets">
        <li>Schmerzlinderung</li><li>Muskelaufbau</li><li>Koordinationsschulung</li><li>Konditionsaufbau</li>
        <li>Verbesserung der Beweglichkeit (Sehnen, Bänder und Gelenke)</li><li>Lösen von Blockaden</li><li>Prävention</li>
        <li>Gangschulung</li><li>Nachsorge nach Operationen</li><li>Wundheilungsstörungen</li><li>Muskelverspannungen</li>
        <li>neurologische Erkrankungen</li><li>degenerative Erkrankungen</li>
      </ul>
      <h2 class="section-title">Hundephysiotheraphie<br>Therapieformen:</h2>
      <ul class="bullets">
        <li>therapeutische Massage</li><li>manuelle Therapie</li><li>passives Bewegen</li><li>aktives Bewegen</li>
        <li>passive Dehnungen</li><li>aktive Dehnungen</li><li>Gelenkmobilisation</li><li>Kältetherapie</li>
        <li>Wärmetherapie</li><li>Narbenbehandlung</li><li>Kinesio Taping / Vet taping</li><li>Behandlung mit Vibrotherm</li><li>u.v.m.</li>
      </ul>
      <p class="note">Dazu biete ich weiterhin eine Magnetfeldtherapie an. Diese unterstützt bei Verspannungen, aktuen Verletzungen, Schmerzen u.v.m.</p>
      <h2 class="section-title">Wirkung:</h2>
      <ul class="bullets">
        <li>Aktivierung von Stoffwechsel und Durchblutung</li><li>Schmerzlinderung</li><li>keimabtötend</li>
        <li>Stimulierung der Angioneogenese (Neubildung von Zellen und Gewebe)</li>
      </ul>
    </div>
    <div class="silhouette" role="img" aria-label="Silhouette eines springenden Hundes"></div>
  </section>

  <div class="photo-circle photo-circle--one" role="img" aria-label="Foto: Therapeutin behandelt einen liegenden Spaniel auf der Wiese"></div>
  <div class="photo-circle photo-circle--two" role="img" aria-label="Foto: Hund steht auf Balancepads im Garten"></div>
  <div class="photo-circle photo-circle--three" role="img" aria-label="Foto: Therapeutin massiert einen Hund auf einer Decke"></div>

  <section class="panel panel--about">
    <svg class="wave" viewBox="0 0 260 150" aria-hidden="true" style="right:-0px">
      <path d="M0 0 L260 0 L260 150 C200 120 190 60 120 60 C60 60 20 40 0 0 Z" fill="var(--cream)"/>
    </svg>
    <div class="about-block">
      <h2 class="about-title" style="margin-top:50px">Hundeosteopathie</h2>
      <ul class="bullets">
        <li>Aktuell befinde ich mich in der Ausbildung zur Hundeosteopathin.</li>
        <li>Natürlich werde ich schon jetzt einige gelernte Anwendungen in meiner Behandlung miteinfließen lassen.</li>
        <li>Prüfung voraussichtlich im Mai 2023</li>
      </ul>
      <p class="about-text">Für mich steht Dein Hund an erster Stelle! Ich habe selbst Erfahrungen mit Tierschutzhunden, sowie Hunden aus deutscher Zucht und weiß, dass manche Hunde "ihr Päckchen" zu tragen haben. Umso mehr möchte ich, dass sich Dein Vierbeiner bei mir wohlfühlt, er mir Vertrauen schenkt und gerne zur Physiotherapie geht.</p>
      <h2 class="about-title">Dorn Therapie und Breuß Massage</h2>
      <ul class="bullets"><li>Ergänzend zur Physiotheraphie</li><li>Breuß-Massage:</li></ul>
      <p class="about-text">Bei der Breuß-Massage wird die Wirbelsäule durch eine wohltuende Massage am Kreuzbein entspannt und gestreckt. Durch gezielte Griffe und Dehnungen wird der Rücken gelockert und verschobene Wirbel schmerzfrei in die ursprüngliche Position gebracht.</p>
      <ul class="bullets"><li>Dorn-Theraphie:</li></ul>
      <p class="about-text">Die Wirbelsäulentherapie nach Dorn, ist eine sanfte Methode, die zur Behandlung von Beschwerden des Bewegungsapparates zum Einsatz kommt. Der Therapeut bringt in der Therapiesitzung Wirbel und Gelenke mit sanften und einfühlsamen Bewegungen in ihre richtige Position zurück.</p>
      <h2 class="about-title">Hundefitnesstrainer (i.A.)</h2>
      <ul class="bullets">
        <li>Perfekte Ergänzung nach erfolgreicher Hundephysiotherapie</li>
        <li>individuelle Trainingspläne</li><li>Muskelaufbautraining</li><li>Beweglichkeitstraining</li><li>Abnehmtraining</li>
        <li>Fitnesstraining</li><li>Gehirntraining</li><li>Schult den optimalen Bewegungsablauf</li>
        <li>Tipps und Training für Sporthunde</li><li>z.B. mit Cavaletti oder Balancepads</li>
      </ul>
    </div>
  </section>
  <p class="footer">Mara Hollweg, Birkenweg 7, 35390 Talheim</p>
</main>

</body>
</html>
```